Classy, Elegant, Simple Business Card Design

Looking to have a classy, simple, and elegant design. Want a top notch designed business card. I really like the look of the new torvane credit card. I also like the design I attached. I am trying to reach 21-29 year old females for booking us for there wedding or event. We offer Disc Jockey Service, Photo Booth Rentals, and Uplighting .

Target Market(s)

21-28 year old females

Contact Information for Business Card

Has to have logo, website, email, and phone number

Font styles to use
Other font styles liked:
• open to font choice, modern, clean
Designer to choose
33a6d7
0791cd
0555a3
ffffff

Requirements
Must have
• Has to have logo, website, email, and phone number
Nice to have
• I really like the design of the new torvane credit card. I also included my logo and some designs I like
Should not have
• clutter or too much info

```html
<!DOCTYPE html>
<html lang="en">
<head>
<meta charset="utf-8">
<title>Tidecrest Event Group – Business Card</title>
<link rel="stylesheet" href="https://fonts.googleapis.com/css2?family=Poppins:wght@300;400;500&display=swap">
<style>
  :root {
    --sky: #33a6d7;
    --blue: #0791cd;
    --deep: #0555a3;
    --white: #ffffff;
    --ink: #4a4a4a;
    --muted: #9a9a9a;
    --backdrop: #e4e4e4;
    --night-top: #2a2b2e;
    --night-bottom: #1a1b1d;
  }
  * { box-sizing: border-box; margin: 0; padding: 0; }
  html, body {
    width: 1200px; height: 1200px; overflow: hidden;
    background: var(--backdrop);
    font-family: "Poppins", sans-serif;
  }
  .canvas { position: relative; width: 1200px; height: 1200px; }
  .card {
    position: absolute; left: 262px; width: 686px; height: 392px;
    overflow: hidden;
  }
  .card-front { top: 165px; background: var(--white); }
  .card-back {
    top: 653px;
    background: linear-gradient(180deg, var(--night-top), var(--night-bottom));
  }

  .divider {
    position: absolute; left: 352px; top: 48px; bottom: 48px; width: 2px;
    background: linear-gradient(180deg, var(--deep), var(--sky), var(--blue));
  }

  .brand {
    position: absolute; left: 380px; top: 118px; width: 280px;
    text-align: center;
  }
  .brand-name {
    color: var(--deep); font-weight: 500; font-size: 22px;
    letter-spacing: 0.3px; line-height: 1.2; white-space: nowrap;
  }
  .services {
    margin-top: 44px; color: var(--ink); font-weight: 400;
    font-size: 16px; line-height: 20px; white-space: nowrap;
  }
  .services .dot {
    display: inline-block; width: 5px; height: 5px; border-radius: 50%;
    background: var(--blue); vertical-align: middle; margin: 0 3px;
  }

  .person { position: absolute; left: 51px; top: 225px; }
  .person-name { color: var(--blue); font-weight: 500; font-size: 24px; line-height: 1.2; }
  .person-title { color: var(--muted); font-weight: 400; font-size: 16px; line-height: 1.2; }
  .contacts { list-style: none; margin-top: 20px; }
  .contacts li {
    display: flex; align-items: center; gap: 13px;
    color: var(--ink); font-size: 16.5px; line-height: 20px;
  }
  .contacts svg { width: 15px; height: 15px; flex: none; }

  .back-name {
    position: absolute; inset: 0; display: flex; align-items: center;
    justify-content: center; color: var(--blue); font-weight: 500;
    font-size: 64px; letter-spacing: 1px;
  }
</style>
</head>
<body>
<main class="canvas">
  <section class="card card-front">
    <div class="divider" aria-hidden="true"></div>

    <div class="brand">
      <p class="brand-name">Tidecrest Event Group</p>
      <p class="services">Disc Jockey Service<br>Photo Booth Rentals<span class="dot"></span>Uplighting</p>
    </div>

    <div class="person">
      <p class="person-name">Daniel Hart</p>
      <p class="person-title">President</p>
      <ul class="contacts">
        <li>
          <svg viewBox="0 0 16 16" aria-hidden="true"><path fill="#0791cd" d="M1 5c0-2 3-3 7-3s7 1 7 3v1h-3V5H4v1H1zM4 7h8l2 6H2z"/><circle cx="8" cy="10" r="1.6" fill="#fff"/></svg>
          <span>555-014-2837</span>
        </li>
        <li>
          <svg viewBox="0 0 16 16" aria-hidden="true"><rect x="1" y="3" width="14" height="10" fill="#0791cd"/><path d="M1 3l7 6 7-6" fill="none" stroke="#fff" stroke-width="1.3"/></svg>
          <span>hello@tidecrestevents.com</span>
        </li>
        <li>
          <svg viewBox="0 0 16 16" aria-hidden="true"><circle cx="8" cy="8" r="7" fill="#0791cd"/><path d="M5 4c2 1 1 3 3 3s1 3 3 4M9 3c1 1 3 1 3 3" fill="none" stroke="#fff" stroke-width="1.2"/></svg>
          <span>www.tidecrestevents.com</span>
        </li>
      </ul>
    </div>
  </section>

  <section class="card card-back">
    <p class="back-name">Tidecrest</p>
  </section>
</main>
</body>
</html>
```